Financial Services Consultant needs a business card

We need a business card for a new consulting company based in Melbourne called
"Quelbrook Insights". Tagline is Clarity for Every Dollar
We would like to see business card designs that are in line with the minimal style of the website www.quelbrook-insights.example
The font I have used on the website is Proxima Nova and would like the same or similar font used on the business card with a minimal design in line with the website Two sided with "QUELBROOK INSIGHTS" CLARITY FOR EVERY DOLLAR on one side and name, title and contact details on the otther
Updates

Hi All, thanks for your submissions, much appreciated.

I have recently added some colour to my webiste, it is hex #3a7b74 for those that wish to use it
Thanks

Hi all

thanks very much for your design submissions I am very impressed and they are much appreciated.

Interms of general feedback please find below;

Colour: I am trying to stick to a minimal design and colour scheme for my website which is still under construction, up to 3 colours( www.quelbrook-insights.example) it is currently black and white with a small amount of blue/green but I am open to suggestion/interpretations for a consulting company.

Card: I dont mind if it has rounded edges or straight, I was thinking about using a letterpress card if possible

Detail: the detail on the card will include; Name, Title, Mobile, Personal Email, Business Email,Web,Business Address

Once again thanks for submissions

Industry/Entity Type

Business

```html
<!DOCTYPE html>
<html lang="en">
<head>
<meta charset="utf-8">
<title>Quelbrook Insights — Business Card</title>
<link rel="stylesheet" href="https://fonts.googleapis.com/css2?family=Open+Sans:wght@400;600;700&display=swap">
<style>
  :root {
    --canvas-bg: #ecebe8;
    --card-dark: #231f20;
    --card-light: #ffffff;
    --ink: #111111;
    --ink-soft: #4a4a4a;
    --on-dark: #ffffff;
    --on-dark-soft: #d9d9d9;
    --divider: #8a8a8a;
    --accent: #3a7b74;
    --card-shadow: 0 6px 18px rgba(0, 0, 0, 0.14);
  }
  * { box-sizing: border-box; margin: 0; padding: 0; }
  html, body {
    width: 1200px;
    height: 720px;
    overflow: hidden;
    background: var(--canvas-bg);
  }
  .canvas {
    position: relative;
    width: 1200px;
    height: 720px;
  }
  .card {
    position: absolute;
    top: 205px;
    width: 540px;
    height: 309px;
    box-shadow: var(--card-shadow);
    font-family: "Open Sans", Arial, sans-serif;
  }

  /* Contact side */
  .card--contact {
    left: 45px;
    background: var(--card-dark);
    color: var(--on-dark);
  }
  .person {
    position: absolute;
    left: 36px;
    top: 206px;
  }
  .person__name {
    font-size: 17px;
    font-weight: 700;
    line-height: 1.2;
  }
  .person__title {
    font-size: 12px;
    color: var(--on-dark-soft);
    margin-top: 2px;
  }
  .person__web {
    font-size: 12px;
    color: var(--on-dark-soft);
    margin-top: 10px;
  }
  .divider {
    position: absolute;
    left: 332px;
    top: 160px;
    width: 1px;
    height: 88px;
    background: var(--divider);
  }
  .contact-list {
    position: absolute;
    left: 350px;
    top: 164px;
    list-style: none;
    font-size: 12px;
    line-height: 1.55;
    color: var(--on-dark-soft);
  }
  .contact-list__phone {
    display: flex;
    align-items: center;
    gap: 6px;
    margin-bottom: 8px;
  }
  .contact-list__phone svg { width: 11px; height: 11px; }

  /* Brand side */
  .card--brand {
    left: 615px;
    background: var(--card-light);
    color: var(--ink);
  }
  .brand {
    position: absolute;
    left: 0;
    width: 100%;
    top: 96px;
    display: flex;
    align-items: center;
    justify-content: center;
    gap: 12px;
  }
  .brand__square {
    width: 16px;
    height: 16px;
    background: var(--accent);
  }
  .brand__name {
    font-size: 30px;
    font-weight: 600;
    letter-spacing: 0;
    line-height: 1;
    color: var(--ink);
    white-space: nowrap;
  }
  .tagline {
    position: absolute;
    left: 0;
    width: 100%;
    top: 148px;
    text-align: center;
    font-size: 14px;
    color: var(--ink-soft);
  }
  .domain {
    position: absolute;
    right: 62px;
    top: 174px;
    font-size: 13px;
    letter-spacing: 1.5px;
    color: var(--ink-soft);
  }
  .domain strong { font-weight: 700; color: var(--ink); }
  .web-address {
    position: absolute;
    left: 0;
    width: 100%;
    top: 246px;
    text-align: center;
    font-size: 13px;
    letter-spacing: 2px;
    color: var(--ink-soft);
  }
  .web-address strong { font-weight: 700; color: var(--ink); }
</style>
</head>
<body>
<main class="canvas">
  <section class="card card--contact" aria-label="Card back with contact details">
    <div class="person">
      <p class="person__name">Your Name</p>
      <p class="person__title">Title</p>
      <p class="person__web">www.quelbrook-insights.example</p>
    </div>
    <div class="divider"></div>
    <ul class="contact-list">
      <li class="contact-list__phone">
        <svg viewBox="0 0 12 12" aria-hidden="true">
          <circle cx="6" cy="6" r="5.3" fill="none" stroke="currentColor" stroke-width="1.2"/>
          <path d="M4 3.2 L5.1 3.2 L5.5 4.8 L4.8 5.3 Q5.5 6.8 6.8 7.3 L7.3 6.6 L8.8 7 L8.8 8.2 Q6.4 8.6 4.6 6.8 Q3.5 5.2 4 3.2 Z" fill="currentColor"/>
        </svg>
        <span>123-456-0789</span>
      </li>
      <li>Street Name, City Name</li>
      <li>State Zip Code</li>
    </ul>
  </section>

  <section class="card card--brand" aria-label="Card front with company name">
    <div class="brand">
      <span class="brand__square" aria-hidden="true"></span>
      <h1 class="brand__name">Quelbrook Insights</h1>
    </div>
    <p class="tagline">Clarity for Every Dollar</p>
    <p class="domain"><strong>quelbrook-insights</strong>.example</p>
    <p class="web-address">www.<strong>quelbrook-insights</strong>.example</p>
  </section>
</main>
</body>
</html>
```